Business Card Design for The Lending Nest Inc.

We need a business card design for our mortgage company: "The Lending Nest Inc."

Need to have Social Media Account on there as a possibility

```html
<!DOCTYPE html>
<html lang="en">
<head>
<meta charset="utf-8">
<title>The Lending Nest Inc. – Business Card</title>
<link rel="stylesheet" href="https://fonts.googleapis.com/css2?family=Open+Sans:wght@400;600&display=swap">
<style>
  :root {
    --page: #ffffff;
    --card-light-top: #f7f7f7;
    --card-light-mid: #ececec;
    --card-light-bottom: #f3f2f3;
    --card-dark: #3b3b3b;
    --brand-blue: #1f5aa6;
    --bar-1: #565656;
    --bar-2: #5f5f5f;
    --bar-3: #6b6b6b;
    --bar-4: #7a7a7a;
    --bar-5: #888888;
    --bar-6: #979595;
    --social-green: #9ccb2f;
    --white: #ffffff;
  }
  * { margin: 0; padding: 0; box-sizing: border-box; }
  html, body {
    width: 1200px; height: 1200px; overflow: hidden;
    background: var(--page);
    font-family: "Open Sans", Arial, sans-serif;
  }
  .canvas { position: relative; width: 1200px; height: 1200px; }

  /* Front face */
  .card-front {
    position: absolute; left: 246px; top: 154px; width: 727px; height: 394px;
    background: linear-gradient(180deg, var(--card-light-top) 0%, var(--card-light-mid) 45%, var(--card-light-bottom) 100%);
  }
  .contact-list { position: absolute; left: 0; top: 88px; list-style: none; }
  .contact-row { display: flex; height: 31px; margin-bottom: 1.5px; }
  .contact-text {
    width: 319px; height: 100%;
    display: flex; align-items: center; justify-content: flex-end;
    padding-right: 6px;
    color: var(--white); font-size: 14.5px; letter-spacing: -0.6px;
    white-space: nowrap;
  }
  .contact-icon {
    width: 31px; height: 100%; margin-left: 2px;
    display: flex; align-items: center; justify-content: center;
  }
  .row-1 .contact-text, .row-1 .contact-icon { background: var(--bar-1); }
  .row-2 .contact-text, .row-2 .contact-icon { background: var(--bar-2); }
  .row-3 .contact-text, .row-3 .contact-icon { background: var(--bar-3); }
  .row-4 .contact-text { background: var(--bar-4); }
  .row-5 .contact-text { background: var(--bar-5); }
  .row-6 .contact-text { background: var(--bar-6); }
  .contact-icon.social { background: var(--social-green); }

  .front-brand { position: absolute; left: 388px; top: 116px; display: flex; align-items: center; }
  .brand-dot {
    width: 68px; height: 68px; border-radius: 50%;
    border: 3px solid var(--brand-blue); flex: none;
  }
  .front-brand .brand-name {
    margin-left: 12px; color: var(--brand-blue);
    font-weight: 600; font-size: 23px; letter-spacing: -0.3px;
    white-space: nowrap;
  }
  .front-tagline {
    position: absolute; left: 396px; top: 208px;
    color: var(--brand-blue); font-size: 32px; font-weight: 400; letter-spacing: -0.3px;
    white-space: nowrap;
  }

  /* Back face */
  .card-back {
    position: absolute; left: 228px; top: 626px; width: 745px; height: 447px;
    background: var(--card-dark);
  }
  .back-brand { position: absolute; left: 26px; top: 72px; display: flex; align-items: center; }
  .back-brand .brand-dot { width: 164px; height: 164px; border-width: 6px; }
  .back-brand .brand-name {
    margin-left: 28px; color: var(--brand-blue);
    font-weight: 600; font-size: 44px; letter-spacing: -0.8px; line-height: 1.05;
  }
  .back-tagline {
    position: absolute; left: 82px; top: 236px;
    color: var(--white); font-size: 74px; font-weight: 400; letter-spacing: -1px;
    white-space: nowrap;
  }
</style>
</head>
<body>
<main class="canvas">

  <section class="card-front">
    <ul class="contact-list">
      <li class="contact-row row-1">
        <span class="contact-text">00.555.014.278.</span>
        <span class="contact-icon">
          <svg width="14" height="18" viewBox="0 0 14 18"><path d="M3 1 L6 1 L7 5 L5 6.5 C5.5 9.5 7 12 9 13.5 L11 12 L13.5 14.5 L12 17 C6 16.5 1 9 2 2 Z" fill="none" stroke="#fff" stroke-width="1.4"/></svg>
        </span>
      </li>
      <li class="contact-row row-2">
        <span class="contact-text">info@lendingnest.com</span>
        <span class="contact-icon">
          <svg width="18" height="13" viewBox="0 0 18 13"><rect x="0.5" y="0.5" width="17" height="12" fill="#fff"/><path d="M0.5 0.5 L9 7.5 L17.5 0.5 M0.5 12.5 L6.5 6 M17.5 12.5 L11.5 6" fill="none" stroke="#6b6b6b" stroke-width="1"/></svg>
        </span>
      </li>
      <li class="contact-row row-3">
        <span class="contact-text">www.lendingnest.com</span>
        <span class="contact-icon">
          <svg width="18" height="18" viewBox="0 0 18 18" fill="none" stroke="#fff" stroke-width="1"><circle cx="9" cy="9" r="8"/><ellipse cx="9" cy="9" rx="3.5" ry="8"/><path d="M1 9 H17 M2.5 5 H15.5 M2.5 13 H15.5"/></svg>
        </span>
      </li>
      <li class="contact-row row-4">
        <span class="contact-text">friendly.net/lendingnest</span>
        <span class="contact-icon social" role="img" aria-label="Social network badge"></span>
      </li>
      <li class="contact-row row-5">
        <span class="contact-text">chirpline.net/lendingnest</span>
        <span class="contact-icon social" role="img" aria-label="Social network badge"></span>
      </li>
      <li class="contact-row row-6">
        <span class="contact-text">worklink.net/lendingnest</span>
        <span class="contact-icon social" role="img" aria-label="Social network badge"></span>
      </li>
    </ul>

    <div class="front-brand">
      <span class="brand-dot"></span>
      <span class="brand-name">The Lending Nest Inc.</span>
    </div>
    <p class="front-tagline">Lending Nest Inc</p>
  </section>

  <section class="card-back">
    <div class="back-brand">
      <span class="brand-dot"></span>
      <span class="brand-name">The Lending<br>Nest Inc.</span>
    </div>
    <p class="back-tagline">Lending Nest Inc</p>
  </section>

</main>
</body>
</html>
```